American cannabis tech company business card design

Pavrel.com is seeking a modern, professional, and brand-aligned business card that represents our company and its core values: Mission, Story, Values, and Impact. As an innovative cannabis company, we want a business card that is not only visually appealing but also serves as a representation of who we are and what we stand for.

Project Scope: Design a double-sided business card that integrates our brand identity and core values. Incorporate our key brand elements, ensuring a sleek and contemporary aesthetic. Visually reflect our core values (Mission, Story, Values, Impact) in a way that is engaging yet professional.

Target Market(s)

Vendors, third parties,

Contact Information for Business Card

Contact details (name, title, email, phone, website, etc.)

Font styles to use
Other font styles liked:
• Caslon, Centra

Colors

Designer to choose colors to be used in the design.

Requirements
Must have
• Pavrel.com logo and branding A creative yet clean way to integrate our core values (Mission, Story, Values, Impact) Modern typography and a well-structured layout
Nice to have
• forest green, grey, white, black
Should not have
• references to marijuana, leafs, plants, or related product

```html
<!DOCTYPE html>
<html lang="en">
<head>
<meta charset="utf-8">
<title>Pavrel.com Business Card</title>
<link rel="stylesheet" href="https://fonts.googleapis.com/css2?family=Roboto:wght@400;700;900&display=swap">
<style>
  :root {
    --forest: #1b3319;
    --forest-dark: #15291a;
    --white: #ffffff;
    --grey: #5c5a5b;
    --grey-text: #8a8a8a;
    --ink: #333333;
    --stage: #3b3b3b;
  }
  * { margin: 0; padding: 0; box-sizing: border-box; }
  html, body {
    width: 1200px;
    height: 689px;
    overflow: hidden;
    background: var(--stage);
    font-family: "Roboto", Arial, sans-serif;
  }
  .sheet {
    width: 1200px;
    height: 689px;
    display: flex;
    align-items: center;
    justify-content: center;
    gap: 40px;
  }
  .card {
    position: relative;
    width: 540px;
    height: 309px;
    border-radius: 16px;
    overflow: hidden;
  }
  .card-front {
    background: var(--forest);
    display: flex;
    align-items: center;
    justify-content: center;
  }
  .wordmark {
    font-weight: 900;
    letter-spacing: 1px;
    text-transform: uppercase;
  }
  .card-front .wordmark {
    color: var(--white);
    font-size: 92px;
  }
  .card-back { background: var(--white); }
  .back-shape {
    position: absolute;
    inset: 0;
    width: 100%;
    height: 100%;
  }
  .back-content {
    position: absolute;
    left: 58px;
    top: 78px;
  }
  .card-back .wordmark {
    color: var(--forest);
    font-size: 50px;
    line-height: 1;
  }
  .holder { margin-top: 44px; }
  .holder-name {
    color: var(--forest);
    font-weight: 700;
    font-size: 21px;
  }
  .holder-title {
    color: var(--grey-text);
    font-size: 13px;
    margin-top: 2px;
  }
  .contact-list {
    list-style: none;
    margin-top: 22px;
  }
  .contact-list li {
    display: flex;
    align-items: center;
    gap: 8px;
    color: var(--ink);
    font-size: 13px;
    line-height: 19px;
  }
  .contact-list svg { width: 11px; height: 11px; flex: none; }
</style>
</head>
<body>
<main class="sheet">
  <section class="card card-front" aria-label="Card front">
    <span class="wordmark">Pavrel</span>
  </section>

  <section class="card card-back" aria-label="Card back">
    <svg class="back-shape" viewBox="0 0 540 309" preserveAspectRatio="none" aria-hidden="true">
      <rect width="540" height="309" fill="var(--grey)"/>
      <path d="M0 0 H440 Q545 110 480 309 H0 Z" fill="var(--forest)"/>
      <path d="M0 0 H400 Q520 120 455 309 H0 Z" fill="var(--white)"/>
    </svg>
    <div class="back-content">
      <div class="wordmark">Pavrel</div>
      <div class="holder">
        <div class="holder-name">Evan Marlow</div>
        <div class="holder-title">President</div>
      </div>
      <ul class="contact-list">
        <li>
          <svg viewBox="0 0 12 12" aria-hidden="true"><path d="M2.5 1 L4.5 1 L5 3.5 L3.8 4.4 Q4.8 6.8 7.6 8.2 L8.5 7 L11 7.5 L11 9.5 Q11 11 9.5 11 Q1 10 1 2.5 Q1 1 2.5 1 Z" fill="var(--forest)"/></svg>
          +1 405-555-0182
        </li>
        <li>
          <svg viewBox="0 0 12 12" aria-hidden="true"><rect x="0.5" y="2" width="11" height="8" fill="var(--forest)"/><path d="M0.8 2.4 L6 6.6 L11.2 2.4" fill="none" stroke="var(--white)" stroke-width="1"/></svg>
          team@pavrel.com
        </li>
        <li>
          <svg viewBox="0 0 12 12" aria-hidden="true"><circle cx="6" cy="6" r="5.5" fill="var(--forest)"/><path d="M0.5 6 H11.5 M6 0.5 Q3 6 6 11.5 M6 0.5 Q9 6 6 11.5" fill="none" stroke="var(--white)" stroke-width="0.8"/></svg>
          www.Pavrel.com
        </li>
      </ul>
    </div>
  </section>
</main>
</body>
</html>
```